BUSINESS CARD - HALLORAN FIELD SERVICES

I would like to create a business card for my fertilizer spreading business. I would like to incorporate my existing logo and also a description of the services offered. The business card will be given to farmers so must be kept simple but effective. It will also be left in stores so much also be eye catching in order to stand out from other cards.

Target Market(s)

FARMERS

Requirements
Must have
• FRONT OF CARD = EXISTING LOGO + "CUSTOMISED SPREADING" below the logo

REAR Of CARD = SERVICES OFFERED AND CONTACT DETAILS

- Bulk fertilizer including Lime, Gypsum, Manure & Compost
- Granular fertilizer including Single Super, Urea, Gran-am, & Custom Blends
- Modern equipment - Autosteer & Variable Rate Capable
- Friendly & Reliable Service
- Contact Gus: 0417 552 308
Nice to have
• utilize same color scheme as existing logo

```html
<!DOCTYPE html>
<html lang="en">
<head>
<meta charset="utf-8">
<title>Halloran Field Services – Business Card</title>
<link href="https://fonts.googleapis.com/css2?family=Montserrat:wght@400;500;700&display=swap" rel="stylesheet">
<style>
  :root {
    --orange-top: #f8a634;
    --orange-bottom: #f7941d;
    --charcoal: #58585a;
    --charcoal-dark: #4b4b4d;
    --ink: #5d5d5f;
    --white: #ffffff;
    --backdrop: #ece8e3;
  }
  * { box-sizing: border-box; margin: 0; padding: 0; }
  html, body { width: 1200px; height: 1200px; overflow: hidden; }
  body {
    background: var(--backdrop);
    font-family: "Montserrat", sans-serif;
    position: relative;
  }
  .card {
    position: absolute;
    left: 257px;
    width: 686px;
    height: 392px;
    border-radius: 22px;
    overflow: hidden;
    box-shadow: 0 10px 24px rgba(0,0,0,0.18);
  }
  .card--front { top: 165px; background: var(--white); }
  .card--back { top: 653px; background: var(--charcoal); color: var(--white); }

  .front-panel {
    position: absolute; inset: 0;
    width: 100%; height: 100%;
  }
  .contact {
    position: absolute; left: 33px; top: 72px; color: var(--white);
  }
  .contact__name { font-size: 22px; font-weight: 700; letter-spacing: 0.2px; }
  .contact__role { font-size: 15px; font-weight: 400; margin-top: 3px; }
  .contact__details { margin-top: 14px; font-size: 15px; line-height: 19px; font-weight: 400; }

  .brand {
    position: absolute; left: 340px; top: 256px; width: 300px; text-align: center;
  }
  .brand__name {
    font-size: 25px; font-weight: 700; color: var(--ink); line-height: 28px; letter-spacing: -0.3px;
  }
  .brand__tagline {
    margin-top: 12px; font-size: 15px; font-weight: 400; letter-spacing: 2px; color: var(--ink);
  }

  .back-brand { position: absolute; left: 29px; top: 38px; width: 300px; }
  .back-brand__name { font-size: 30px; font-weight: 700; line-height: 33px; letter-spacing: -0.4px; }
  .back-brand__tagline { margin-top: 10px; font-size: 14.5px; letter-spacing: 4.8px; font-weight: 400; }

  .services {
    position: absolute; left: 29px; top: 165px; list-style: none; font-size: 14.5px; line-height: 19px;
  }
  .services li { position: relative; padding-left: 18px; margin-bottom: 19px; }
  .services li::before {
    content: ""; position: absolute; left: 2px; top: 6px; width: 6px; height: 6px;
    border-radius: 50%; background: var(--white);
  }
</style>
</head>
<body>
  <section class="card card--front" aria-label="Business card front">
    <svg class="front-panel" viewBox="0 0 686 392" preserveAspectRatio="none" aria-hidden="true">
      <defs>
        <linearGradient id="orangeFill" x1="0" y1="0" x2="0" y2="1">
          <stop offset="0" stop-color="#f8a634"/>
          <stop offset="1" stop-color="#f7941d"/>
        </linearGradient>
      </defs>
      <path d="M0 0 H440 C330 60 200 210 235 392 H0 Z" fill="url(#orangeFill)"/>
    </svg>
    <div class="contact">
      <p class="contact__name">GUS HALLORAN</p>
      <p class="contact__role">President</p>
      <p class="contact__details">0417 552 308<br>info@halloranfield.com<br>www.halloranfield.com</p>
    </div>
    <div class="brand">
      <p class="brand__name">Halloran Field<br>Services</p>
      <p class="brand__tagline">CUSTOMISED SPREADING</p>
    </div>
  </section>

  <section class="card card--back" aria-label="Business card back">
    <div class="back-brand">
      <p class="back-brand__name">Halloran Field Services</p>
      <p class="back-brand__tagline">CUSTOMISED SPREADING</p>
    </div>
    <ul class="services">
      <li>Bulk fertilizer including Lime,<br>Gypsum, Manure &amp; Compost</li>
      <li>Granular fertilizer including Single<br>Super, Urea, Gran-am, &amp; Custom Blends</li>
      <li>Modern equipment -<br>Autosteer &amp; Variable Rate Capable</li>
      <li>Friendly &amp; Reliable Service</li>
    </ul>
  </section>
</body>
</html>
```